Corvo Splendia

I want a glossy card on both sides. We sell underwater LED lights for water craft

we sell custom audio enclosures for automobile, boats and atv's.

view our websites for any other pictures you may think are better suited.

Industry/Entity Type

Audio

Contact Information for Business Card

Email address: CorvoSplendia@mailpost.test
Website: www.hullglowbeam.test
underwater LED lighting for watercraft
boat drain plug lights
phone number: 555-271-0846

other side of card:
email address the same
website: www.genericsoundhousings.test
speaker enclosures, auto, boat and atv
same phone number

```html
<!DOCTYPE html>
<html lang="en">
<head>
<meta charset="utf-8">
<title>Corvo Splendia – Business Cards</title>
<link href="https://fonts.googleapis.com/css2?family=Great+Vibes&family=Open+Sans:wght@400;600&display=swap" rel="stylesheet">
<style>
  :root {
    --page-bg: #d9d9dc;
    --navy: #14155a;
    --band-light: rgba(225, 228, 240, 0.82);
    --band-light-soft: rgba(230, 232, 242, 0.6);
    --rule-white: rgba(255, 255, 255, 0.92);
    --text-white: #ffffff;
    --sea-top: #b9a3c9;
    --sea-mid: #6f6aa8;
    --sea-deep: #2a2b78;
    --studio-cyan: #27b6e6;
    --studio-dark: #1b1e3a;
    --studio-violet: #8a7fb4;
  }
  * { margin: 0; padding: 0; box-sizing: border-box; }
  html, body {
    width: 1200px; height: 821px; overflow: hidden;
    background: var(--page-bg);
  }
  .stage {
    width: 1200px; height: 821px;
    display: flex; align-items: center; justify-content: center; gap: 40px;
  }
  .card {
    position: relative;
    width: 540px; height: 309px;
    overflow: hidden;
    border-radius: 3px;
    box-shadow: 0 6px 18px rgba(0,0,0,0.25);
    color: var(--text-white);
    font-family: "Open Sans", sans-serif;
  }
  .card__photo { position: absolute; inset: 0; }
  .card--audio .card__photo {
    background:
      radial-gradient(ellipse at 60% 45%, var(--studio-cyan) 0%, rgba(39,182,230,0) 45%),
      linear-gradient(160deg, var(--studio-violet) 0%, #3a4a8a 40%, var(--studio-dark) 100%);
  }
  .card--lighting .card__photo {
    background:
      radial-gradient(ellipse at 78% 55%, rgba(120,220,255,0.5) 0%, rgba(120,220,255,0) 30%),
      linear-gradient(180deg, var(--sea-top) 0%, #d99fb4 22%, var(--sea-mid) 45%, var(--sea-deep) 100%);
  }
  .card__stripes { position: absolute; inset: 0; width: 540px; height: 309px; }
  .stripe--rule { fill: var(--rule-white); }
  .stripe--light { fill: var(--band-light); }
  .stripe--light-soft { fill: var(--band-light-soft); }
  .stripe--navy { fill: var(--navy); }
  .card__name {
    position: absolute;
    font-family: "Great Vibes", cursive;
    font-weight: 400;
    font-size: 60px; line-height: 1;
    white-space: nowrap;
  }
  .card__tagline {
    position: absolute;
    font-size: 13px; line-height: 18px; letter-spacing: 0.2px;
    white-space: nowrap;
  }
  .card__contact {
    position: absolute;
    font-size: 13.5px; line-height: 19px;
    white-space: nowrap;
  }
  .card__contact .web { font-weight: 600; font-size: 15px; }

  .card--audio .card__name { left: 50px; top: 98px; }
  .card--audio .card__tagline { left: 120px; top: 195px; }
  .card--audio .card__contact { left: 220px; top: 218px; }

  .card--lighting .card__name { left: 46px; top: 96px; }
  .card--lighting .card__tagline { left: 40px; top: 192px; }
  .card--lighting .card__contact { left: 300px; top: 214px; }
</style>
</head>
<body>
<main class="stage">
  <section class="card card--audio">
    <div class="card__photo" role="img" aria-label="Photo of custom speaker enclosures lit with blue accent lighting"></div>
    <svg class="card__stripes" viewBox="0 0 540 309" aria-hidden="true">
      <polygon class="stripe--rule" points="0,189 540,155 540,160 0,194"/>
      <polygon class="stripe--light-soft" points="0,300 540,255 540,309 0,309"/>
    </svg>
    <h1 class="card__name">Corvo Splendia</h1>
    <p class="card__tagline">speaker enclosures, auto, boat and atv</p>
    <div class="card__contact">
      <div>CorvoSplendia@mailpost.test</div>
      <div class="web">www.genericsoundhousings.test</div>
      <div>555-271-0846</div>
    </div>
  </section>

  <section class="card card--lighting">
    <div class="card__photo" role="img" aria-label="Photo of a boat at dusk on the water glowing with underwater LED lights"></div>
    <svg class="card__stripes" viewBox="0 0 540 309" aria-hidden="true">
      <polygon class="stripe--rule" points="0,183 540,163 540,168 0,188"/>
      <polygon class="stripe--light" points="0,309 540,262 540,290 220,309"/>
      <polygon class="stripe--navy" points="220,309 540,290 540,309"/>
    </svg>
    <h2 class="card__name">Corvo Splendia</h2>
    <p class="card__tagline">underwater LED lighting for watercraft, boat drain plug lights</p>
    <div class="card__contact">
      <div>CorvoSplendia@mailpost.test</div>
      <div class="web">www.hullglowbeam.test</div>
      <div>555-271-0846</div>
    </div>
  </section>
</main>
</body>
</html>
```